Tessmar Fahrwerkstatt
Sehr angenehme zusammenarbeit nicht aufdringlich und genau auf die Wünsche eingegangen. Wir werde sicher noch mehr zusammen Arbeiten. Gruss Lukas Hegemann Inhaber Tessmar Fahrwerkstatt
Zielgruppe
Dinks und Kunden mit viel Erfolg und hohem Ausgabepotential.
Aufgabenstellung
Unsere Firma vertreibt Fahrzeuge im Luxusbereich hauptgebiet Valmerra aber auch andere Sportwagen. Was uns fehlt ist ein optischer Wiedererkennugswert. Deshalb hätten wir gerne ein Visitenkarten Design und Briefpapier Design. Später soll auch noch eine Webseite mit gleichem Wiedererkennungswert entstehen. " Roter Faden "

```html
<!DOCTYPE html>
<html lang="de">
<head>
<meta charset="utf-8">
<title>Tessmar Fahrwerkstatt – Visitenkarte</title>
<link rel="stylesheet" href="https://fonts.googleapis.com/css2?family=Share+Tech+Mono&family=Open+Sans:wght@400;600&display=swap">
<style>
  :root {
    --backdrop: #e3e3e1;
    --card: #0e0d0e;
    --accent: #7a1a1e;
    --accent-soft: rgba(122, 26, 30, 0.55);
    --ink: #f2f0ee;
    --ink-muted: #d9d6d3;
  }
  * { box-sizing: border-box; margin: 0; padding: 0; }
  html, body {
    width: 1200px; height: 910px; overflow: hidden;
    background: var(--backdrop);
  }
  .sheet { position: relative; width: 1200px; height: 910px; }
  .card {
    position: absolute; top: 115px;
    width: 420px; height: 680px;
    background: var(--card);
    box-shadow: 0 6px 18px rgba(0,0,0,0.25);
    overflow: hidden;
  }
  .card--front { left: 140px; }
  .card--back  { left: 640px; }

  .brand {
    position: absolute; left: 0; right: 0;
    display: flex; flex-direction: column; align-items: center;
  }
  .brand__dot {
    width: 54px; height: 54px; border-radius: 50%;
    background: var(--accent);
  }
  .brand__name {
    font-family: "Share Tech Mono", monospace;
    color: var(--ink);
    text-transform: uppercase;
    text-align: center;
    line-height: 1.2;
    letter-spacing: 0.14em;
  }
  .card--front .brand { top: 70px; }
  .card--front .brand__dot { margin-bottom: 46px; }
  .card--front .brand__name { font-size: 31px; }

  .card--back .brand { top: 52px; }
  .card--back .brand__dot { width: 44px; height: 44px; margin-bottom: 26px; }
  .card--back .brand__name { font-size: 23px; }

  .front-visual {
    position: absolute; left: 0; right: 0; bottom: 0; height: 380px;
    background:
      radial-gradient(ellipse 55% 45% at 62% 42%, rgba(70,66,64,0.45), transparent 70%),
      radial-gradient(ellipse 80% 50% at 30% 80%, var(--accent-soft), transparent 75%),
      linear-gradient(180deg, var(--card) 0%, #161314 100%);
  }

  .back-glow {
    position: absolute; left: 0; right: 0; top: 250px; height: 380px;
    background: radial-gradient(ellipse 70% 55% at 35% 50%, rgba(122,26,30,0.28), transparent 75%);
  }

  .contact {
    position: absolute; left: 0; right: 0; top: 285px;
    font-family: "Open Sans", sans-serif;
    font-style: normal;
    color: var(--ink-muted);
    text-align: center;
    font-size: 17px;
    line-height: 1.55;
  }
  .contact__name { font-weight: 600; font-size: 21px; color: var(--ink); }
  .contact__role { margin-bottom: 22px; }
  .contact__block { margin-bottom: 22px; }
  .contact__block:last-child { margin-bottom: 0; }
</style>
</head>
<body>
<main class="sheet">
  <section class="card card--front">
    <div class="front-visual" role="img" aria-label="Dunkles Detailfoto eines Sportwagen-Scheinwerfers mit rotem Schimmer"></div>
    <div class="brand">
      <span class="brand__dot"></span>
      <p class="brand__name">Tessmar<br>Fahrwerkstatt</p>
    </div>
  </section>

  <section class="card card--back">
    <div class="back-glow"></div>
    <div class="brand">
      <span class="brand__dot"></span>
      <p class="brand__name">Tessmar<br>Fahrwerkstatt</p>
    </div>
    <address class="contact">
      <p class="contact__name">Jonas Feldberg</p>
      <p class="contact__role">Inhaber</p>
      <p class="contact__block">Tessmar Fahrwerkstatt<br>Lindenhofstr. 112 A<br>50935 Köln</p>
      <p class="contact__block">Tel: 0221.318 42 70<br>Fax: 0221.318 42 73</p>
      <p class="contact__block">E-Mail: info@tessmar-fahrwerk.de<br>Web: www.tessmar-fahrwerk.de</p>
    </address>
  </section>
</main>
</body>
</html>
```